Elegant Lumocrest Rentals DL flyer

We run a Lumocrest Rentals business - this will be used as a business card as well.

our website is lumocrestrentals.com.au

Front page it sour logo which is attached website details - on the front it needs to say wedding and event hire needs etc..

on the back we will have a spot for 4 products but we want to say there is more so check our the website

A background in the flyer only for example like this would be good http://tapestrova.com/dark-backdrop-image_4726.html

Wedding

Must have
• nice background elegant in style pink and black is the colours

```html
<!DOCTYPE html>
<html lang="en">
<head>
<meta charset="utf-8">
<title>Lumocrest Rentals – DL Flyer</title>
<link href="https://fonts.googleapis.com/css2?family=Questrial&family=Didact+Gothic&display=swap" rel="stylesheet">
<style>
  :root {
    --stage: #4b4b4b;
    --ink: #141414;
    --charcoal: #262626;
    --slate: #4a4a4a;
    --pink: #e0148c;
    --pink-deep: #b00a6c;
    --pink-soft: #ef5fb2;
    --white: #ffffff;
    --plum: #3a0a26;
  }
  * { box-sizing: border-box; margin: 0; padding: 0; }
  html, body { width: 1200px; height: 1036px; overflow: hidden; background: var(--stage); }
  body { position: relative; font-family: "Questrial", "Didact Gothic", sans-serif; }

  .panel {
    position: absolute; top: 27px; width: 496px; height: 985px;
    overflow: hidden; border: 1px solid #d8d8d8;
    box-shadow: 0 0 14px rgba(0,0,0,.55);
  }
  .panel--front { left: 89px; background: var(--ink); }
  .panel--back { left: 617px; background: var(--ink); }
  .panel svg.backdrop { position: absolute; inset: 0; }

  .brand-band {
    position: absolute; left: 0; top: 121px; width: 100%; height: 134px;
    background: linear-gradient(90deg, #2a2a2a 0%, #6a6a6a 45%, #2a2a2a 100%);
    display: flex; align-items: center; justify-content: center; gap: 14px;
  }
  .brand-mark { width: 46px; height: 46px; border-radius: 50%; background: var(--pink); }
  .brand-name { color: var(--white); font-size: 34px; letter-spacing: .5px; }

  .tagline {
    position: absolute; left: 0; top: 498px; width: 100%;
    text-align: center; color: var(--white); font-size: 23px; line-height: 30px;
  }
  .tagline strong { font-weight: 700; font-family: "Didact Gothic", sans-serif; -webkit-text-stroke: .5px var(--white); }

  .contact { position: absolute; left: 0; top: 810px; width: 100%; text-align: center; }
  .contact__web { color: var(--pink); font-size: 28px; font-weight: 700; -webkit-text-stroke: .6px var(--pink); }
  .contact__mail { color: var(--pink); font-size: 20px; margin-top: 4px; }
  .contact__phone {
    display: inline-block; margin-top: 22px; width: 254px; height: 49px; line-height: 49px;
    border-radius: 4px; color: var(--white); font-size: 33px; font-weight: 700; -webkit-text-stroke: .8px var(--white);
    background: linear-gradient(180deg, var(--pink-soft) 0%, var(--pink) 45%, var(--pink-deep) 100%);
  }

  .products-title {
    position: absolute; left: 0; top: 56px; width: 100%; text-align: center;
    color: var(--white); font-size: 29px;
  }
  .product-label { position: absolute; color: var(--pink); font-size: 19px; white-space: nowrap; }
  .product-photo { position: absolute; border: 2px solid #e6e6e6; }
  .photo--cocktail { left: 16px; top: 184px; width: 259px; height: 145px;
    background: linear-gradient(160deg, #c9cbcc 0%, #7b7e80 55%, #3a3c3d 100%); }
  .photo--chair { left: 308px; top: 247px; width: 143px; height: 145px;
    background: radial-gradient(circle at 50% 50%, #f2f2f2 0%, #ffffff 60%); }
  .photo--cubes { left: 24px; top: 376px; width: 228px; height: 145px;
    background: linear-gradient(135deg, #d13a4a 0%, #3bd07a 40%, #35c3d8 65%, #b03ad0 100%); }
  .photo--antique { left: 238px; top: 454px; width: 256px; height: 148px;
    background: linear-gradient(180deg, #e8e9e6 0%, #cfd3cc 45%, #4f6a2e 100%); }

  .callout {
    position: absolute; left: 98px; top: 628px; width: 306px; height: 110px;
    display: flex; align-items: center; justify-content: center; text-align: center;
    color: var(--pink); font-size: 24px; line-height: 31px; font-weight: 700; -webkit-text-stroke: .5px var(--pink);
  }
  .callout svg { position: absolute; inset: 0; }
  .callout span { position: relative; }
</style>
</head>
<body>

<section class="panel panel--front">
  <svg class="backdrop" width="496" height="985" viewBox="0 0 496 985">
    <defs>
      <linearGradient id="frontTop" x1="0" y1="0" x2="0" y2="1">
        <stop offset="0" stop-color="#1a1a1a"/><stop offset="1" stop-color="#2e2e2e"/>
      </linearGradient>
    </defs>
    <rect width="496" height="300" fill="url(#frontTop)"/>
    <path d="M0 300 C120 270 220 360 340 320 C410 296 460 290 496 300 L496 985 L0 985Z" fill="#3a0a26"/>
    <path d="M0 318 C110 300 230 380 350 340 C420 318 470 315 496 322 L496 790 L0 790Z" fill="var(--pink)"/>
    <path d="M0 420 C120 360 250 400 330 470 C400 530 450 560 496 540 L496 600 C420 640 330 580 250 520 C170 460 80 440 0 470Z" fill="#ea3aa0" opacity=".55"/>
    <path d="M0 680 C120 650 260 720 380 700 C440 690 480 680 496 676 L496 790 L0 790Z" fill="#c70f7c"/>
    <path d="M0 770 C140 740 280 800 496 775 L496 985 L0 985Z" fill="var(--ink)"/>
  </svg>

  <div class="brand-band">
    <span class="brand-mark"></span>
    <span class="brand-name">Lumocrest Rentals</span>
  </div>

  <p class="tagline">A range of wedding packages and<br>equipment to make your day<br>special <strong>without the extra cost.</strong></p>

  <div class="contact">
    <p class="contact__web">lumocrestrentals.com.au</p>
    <p class="contact__mail">info@lumocrestrentals.com.au</p>
    <p class="contact__phone">0491570156</p>
  </div>
</section>

<section class="panel panel--back">
  <svg class="backdrop" width="496" height="985" viewBox="0 0 496 985">
    <rect width="496" height="985" fill="var(--slate)"/>
    <path d="M0 0 H496 V130 C380 170 240 120 120 150 C70 162 30 160 0 152Z" fill="var(--pink)"/>
    <path d="M0 152 C60 165 140 150 220 140 C320 128 420 150 496 130 L496 160 C400 190 300 160 200 175 C120 185 50 178 0 170Z" fill="#c70f7c"/>
    <path d="M496 390 C380 420 250 500 150 600 C110 640 60 680 0 700 L0 640 C80 600 160 520 260 460 C340 410 420 390 496 370Z" fill="#5c5c5c"/>
    <path d="M0 700 C110 690 200 730 300 710 C380 694 440 650 496 640 L496 985 L0 985Z" fill="var(--pink)"/>
    <path d="M0 745 C90 730 170 760 250 742 C330 724 420 700 496 720 L496 985 L0 985Z" fill="#ea3aa0" opacity=".55"/>
    <path d="M0 800 C100 775 190 780 260 770 C330 760 420 730 496 745 L496 985 L0 985Z" fill="var(--ink)"/>
    <path d="M260 770 L310 765 L318 790 Z" fill="var(--pink)"/>
    <path d="M300 762 L338 760 L316 792 Z" fill="var(--pink)"/>
  </svg>

  <h2 class="products-title">Some of our products:</h2>

  <p class="product-label" style="left:58px;top:158px;">Cocktail Tables</p>
  <div class="product-photo photo--cocktail" role="img" aria-label="Photo of black cocktail tables with stools"></div>

  <p class="product-label" style="left:292px;top:221px;font-size:17px;">Americana Chairs</p>
  <div class="product-photo photo--chair" role="img" aria-label="Photo of a white folding Americana chair"></div>

  <p class="product-label" style="left:66px;top:350px;">Glow Cubes</p>
  <div class="product-photo photo--cubes" role="img" aria-label="Photo of illuminated coloured glow cubes"></div>

  <p class="product-label" style="left:287px;top:428px;">Antique Tables</p>
  <div class="product-photo photo--antique" role="img" aria-label="Photo of a white antique table on grass"></div>

  <div class="callout">
    <svg width="306" height="110" viewBox="0 0 306 110">
      <path d="M18 6 L296 10 Q304 10 303 18 L290 98 Q289 106 281 106 L8 104 Q1 104 2 96 L10 14 Q11 6 18 6Z" fill="#2f2f2f" stroke="#d9d9d9" stroke-width="2"/>
    </svg>
    <span>Check our website<br>for more !</span>
  </div>

  <div class="contact">
    <p class="contact__web">lumocrestrentals.com.au</p>
    <p class="contact__mail">info@lumocrestrentals.com.au</p>
    <p class="contact__phone">0491570156</p>
  </div>
</section>

</body>
</html>
```